Lanternfield Drinks business cards

We need a business card design for our new logo. The company is modern, progressive, professional, yet approachable. The key products are ready to drink bottles and cans of coffee based beverages.
These cards will be a critical part of the first impression made by our sales organization, business development team, and all external facing personnel.
Card can be a vertical or horizontal orientation.

Target Market(s)

Customers, suppliers, business partners

Industry/Entity Type

Business

Contact Information for Business Card

Business cards should feature Company Name and Logo.

Font styles to use
Serif

Colors

Designer to choose colors to be used in the design.

Requirements
Must have
• Strong readability of Name, phone #, mobile number and email address.
• Job title, website url, Street Address, and other details can be secondary level readability.
Nice to have
• High impact, simplistic quality design.
• Ok to utilize the 'H in the box' separate from the company name

```html
<!DOCTYPE html>
<html lang="en">
<head>
<meta charset="utf-8">
<title>Lanternfield Drinks – Business Cards</title>
<link rel="stylesheet" href="https://fonts.googleapis.com/css2?family=Crimson+Pro:wght@400;600;700&display=swap">
<style>
  :root {
    --backdrop: #bdbdbd;
    --orange-top: #e08a3a;
    --orange-bottom: #c34c2b;
    --brand-red: #c9472a;
    --brand-gold: #e39136;
    --paper: #fbfbf9;
    --ink: #1e1e1e;
    --on-brand: #fbeee6;
  }
  * { margin: 0; padding: 0; box-sizing: border-box; }
  html, body {
    width: 1200px; height: 576px; overflow: hidden;
    background: var(--backdrop);
    font-family: "Crimson Pro", Georgia, serif;
  }
  .canvas { position: relative; width: 1200px; height: 576px; }
  .card {
    position: absolute; border-radius: 12px; overflow: hidden;
    box-shadow: 0 3px 8px rgba(0,0,0,.25);
  }

  /* Front */
  .card-front {
    left: 82px; top: 139px; width: 484px; height: 293px;
    background: linear-gradient(180deg, var(--orange-top), var(--orange-bottom));
  }
  .card-front .brand-square {
    position: absolute; left: 204px; top: 77px; width: 76px; height: 76px;
    border: 4px solid var(--paper);
  }
  .card-front .brand-name {
    position: absolute; left: 0; right: 0; top: 160px; text-align: center;
    color: var(--paper); font-weight: 700; text-transform: uppercase; line-height: 1;
  }
  .card-front .brand-line-1 { display: block; font-size: 40px; letter-spacing: 0.5px; }
  .card-front .brand-line-2 { display: block; font-size: 15px; letter-spacing: 2px; margin-top: 6px; }

  /* Back */
  .card-back {
    left: 602px; top: 138px; width: 482px; height: 292px;
    background: var(--paper);
  }
  .card-back .wave { position: absolute; left: 0; top: 0; }
  .card-back .brand-square {
    position: absolute; left: 108px; top: 43px; width: 72px; height: 71px;
    border: 4px solid var(--brand-red);
  }
  .card-back .brand-name {
    position: absolute; left: 24px; top: 124px; width: 242px; text-align: center;
    color: var(--brand-red); font-weight: 700; text-transform: uppercase; line-height: 1;
  }
  .card-back .brand-line-1 { display: block; font-size: 33px; letter-spacing: 0.3px; }
  .card-back .brand-line-2 { display: block; font-size: 13px; letter-spacing: 2px; margin-top: 4px; }

  .person { position: absolute; right: 22px; top: 41px; text-align: right; }
  .person-name { color: var(--brand-red); font-weight: 700; font-size: 23px; line-height: 1.1; }
  .person-title { color: var(--ink); font-size: 13px; font-weight: 600; margin-top: 2px; }

  .contact-list {
    position: absolute; right: 22px; top: 187px; list-style: none; text-align: right;
    color: var(--on-brand); font-size: 14px; line-height: 17px;
  }
  .contact-list li { display: flex; justify-content: flex-end; align-items: center; gap: 10px; }
  .contact-list svg { width: 11px; height: 11px; fill: none; stroke: var(--on-brand); stroke-width: 1.4; }
  .address {
    position: absolute; right: 22px; top: 262px;
    color: var(--on-brand); font-size: 14px; line-height: 17px;
  }
</style>
</head>
<body>
<main class="canvas">

  <section class="card card-front" aria-label="Card front">
    <div class="brand-square"></div>
    <div class="brand-name">
      <span class="brand-line-1">Lanternfield</span>
      <span class="brand-line-2">Drinks Co</span>
    </div>
  </section>

  <section class="card card-back" aria-label="Card back">
    <svg class="wave" width="482" height="292" viewBox="0 0 482 292">
      <path d="M0 250 C70 270 160 280 240 260 C335 236 385 160 482 154 L482 292 L0 292 Z" fill="var(--brand-red)"/>
      <path d="M0 222 C80 248 160 262 240 244 C330 224 380 150 482 140 L482 148 C385 160 335 234 245 255 C160 274 80 266 0 240 Z" fill="var(--brand-gold)"/>
    </svg>

    <div class="brand-square"></div>
    <div class="brand-name">
      <span class="brand-line-1">Lanternfield</span>
      <span class="brand-line-2">Drinks Co</span>
    </div>

    <div class="person">
      <div class="person-name">Mara Ellison Voss</div>
      <div class="person-title">Managing Director</div>
    </div>

    <ul class="contact-list">
      <li>555.302.4418
        <svg viewBox="0 0 12 12"><path d="M2 2 h2 l1 2.5 -1.2 1 a6 6 0 0 0 2.7 2.7 l1-1.2 2.5 1 v2 a1 1 0 0 1 -1 1 A9 9 0 0 1 1 3 a1 1 0 0 1 1 -1z"/></svg></li>
      <li>555.302.7760
        <svg viewBox="0 0 12 12"><rect x="3" y="1" width="6" height="10" rx="1"/><line x1="5" y1="9" x2="7" y2="9"/></svg></li>
      <li>www.lanternfield.co
        <svg viewBox="0 0 12 12"><rect x="1" y="2.5" width="10" height="7"/><path d="M1 2.5 L6 7 L11 2.5"/></svg></li>
      <li>mara@lanternfield.co
        <svg viewBox="0 0 12 12"><circle cx="6" cy="6" r="5"/><ellipse cx="6" cy="6" rx="2.2" ry="5"/><line x1="1" y1="6" x2="11" y2="6"/></svg></li>
    </ul>

    <div class="address">87 Copperline Ave., Brookhaven, US 40218</div>
  </section>

</main>
</body>
</html>
```